Business Card Design Project

We are rebranding an existing automotive collision repair business. The business is called dent haven. I have attached logo but I'm not tied to that. I want to leave this wide open.

I want this card to say we are professional, competent, cutting edge. We are focused on customers and use a lot of the latest technology to make the customer experience different. We sign customers in on iPads. Paperwork I signed electronically and updates are sent via text, email, logging on a website or as they wish. I want this innovation and image to come through in our cards

Target Market(s)

60%. Women 40% men. Age 35-60

Industry/Entity Type

Automotive

Requirements
Must have
• The card must have name, title, phone,email, cell, web page

```html
<!DOCTYPE html>
<html lang="en">
<head>
<meta charset="utf-8">
<title>Dent Haven Business Card</title>
<link href="https://fonts.googleapis.com/css2?family=Open+Sans:wght@300;400;600;700&display=swap" rel="stylesheet">
<style>
  :root {
    --backdrop: #1f1f1f;
    --green-deep: #23802a;
    --green-mid: #55a02a;
    --green-bright: #80bb25;
    --white: #ffffff;
    --ink: #333333;
    --ink-soft: #5a5a5a;
    --rule: #9a9a9a;
  }
  * { margin: 0; padding: 0; box-sizing: border-box; }
  html, body {
    width: 1200px; height: 900px; overflow: hidden;
    background: var(--backdrop);
    font-family: "Open Sans", Arial, sans-serif;
  }
  .canvas { position: relative; width: 1200px; height: 900px; }
  .card {
    position: absolute; left: 294px; width: 575px; height: 328px;
    border-radius: 22px; overflow: hidden;
  }
  .card-front {
    top: 107px;
    background: radial-gradient(ellipse at 100% 10%, var(--green-bright) 0%, var(--green-bright) 25%, transparent 60%),
                linear-gradient(120deg, var(--green-deep) 0%, var(--green-mid) 45%, var(--green-bright) 80%);
    display: flex; align-items: center; justify-content: center;
  }
  .brand-name {
    font-weight: 700; letter-spacing: -0.5px; line-height: 1;
  }
  .card-front .brand-name { color: var(--white); font-size: 46px; margin-top: 8px; }
  .card-back { top: 457px; background: var(--white); }
  .card-back .brand-name {
    position: absolute; left: 0; width: 296px; top: 148px;
    text-align: center; color: var(--green-bright); font-size: 30px;
  }
  .divider {
    position: absolute; left: 296px; top: 50px; width: 1px; height: 246px;
    background: linear-gradient(to bottom, transparent, var(--rule) 30%, var(--rule) 70%, transparent);
  }
  .details { position: absolute; left: 336px; top: 62px; }
  .person-name { color: var(--green-bright); font-weight: 600; font-size: 21px; line-height: 1.2; }
  .person-title { color: var(--ink); font-size: 14px; font-weight: 400; margin-top: 2px; }
  .address { color: var(--ink-soft); font-weight: 300; font-size: 14px; line-height: 19px; margin-top: 38px; }
  .contacts { list-style: none; margin-top: 14px; }
  .contacts li {
    display: flex; align-items: center; gap: 8px;
    color: var(--ink-soft); font-weight: 300; font-size: 14px; line-height: 20.5px;
  }
  .contacts svg { width: 12px; height: 12px; flex: none; fill: var(--green-bright); }
</style>
</head>
<body>
<main class="canvas">
  <section class="card card-front">
    <span class="brand-name">Dent Haven</span>
  </section>

  <section class="card card-back">
    <span class="brand-name">Dent Haven</span>
    <div class="divider"></div>
    <div class="details">
      <p class="person-name">Marcus Reyes</p>
      <p class="person-title">Vice President</p>
      <p class="address">4170 W. Larkspur Avenue. STE 214<br>PMB#318 Tempe, AZ 85282</p>
      <ul class="contacts">
        <li>
          <svg viewBox="0 0 12 12" aria-hidden="true"><path d="M1 4c0-2 2-2.5 5-2.5S11 2 11 4v1H8.5V4h-5v1H1z"/><path d="M3 6h6l1.5 4.5h-9z"/></svg>
          800-555-0142
        </li>
        <li>
          <svg viewBox="0 0 12 12" aria-hidden="true"><rect x="0.5" y="8" width="2" height="3.5"/><rect x="3.5" y="6" width="2" height="5.5"/><rect x="6.5" y="3.5" width="2" height="8"/><rect x="9.5" y="1" width="2" height="10.5"/></svg>
          800-555-0142
        </li>
        <li>
          <svg viewBox="0 0 12 12" aria-hidden="true"><path d="M0.5 2.5h11v7h-11z M1.5 3.5v5h9v-5L6 6.8z M2.3 3.5 6 5.8l3.7-2.3z" fill-rule="evenodd"/></svg>
          info@denthaven.com
        </li>
        <li>
          <svg viewBox="0 0 12 12" aria-hidden="true"><circle cx="6" cy="6" r="5.5"/><path d="M0.5 6h11M6 0.5v11" stroke="#fff" stroke-width="0.8"/></svg>
          www.denthaven.com
        </li>
      </ul>
    </div>
  </section>
</main>
</body>
</html>
```